Larkfield Ridge Management

I need a professional website. My current website is larkfieldridgemanagement.com and I hate it. It was created with some AI tool very quickly because I needed a site up and running with no advanced notice. I’m open to all designs .. I trust you, the professionals will deliver the results I’m anxiously awaiting! :)

```html
<!DOCTYPE html>
<html lang="en">
<head>
<meta charset="utf-8">
<title>Larkfield Ridge Management</title>
<link href="https://fonts.googleapis.com/css2?family=Montserrat:wght@400;500;600;700&family=Roboto:wght@400;500;700&display=swap" rel="stylesheet">
<style>
:root{
  --navy:#233a6b;
  --navy-dark:#1c2f5a;
  --red:#b4313a;
  --ink:#222;
  --muted:#555;
  --line:#d9d9d9;
  --card:#f3f3f3;
  --footer:#333333;
  --white:#fff;
}
*{margin:0;padding:0;box-sizing:border-box}
html,body{width:1200px;height:5140px;overflow:hidden}
body{position:relative;font-family:"Roboto",Arial,sans-serif;color:var(--ink);background:var(--white)}
.abs{position:absolute}
.heading{font-family:"Montserrat",Arial,sans-serif;font-weight:500;text-align:center;left:0;width:1200px}
.sub{font-size:12.5px;line-height:16px;text-align:center;left:270px;width:660px}
.btn{position:absolute;background:var(--red);color:#fff;font-family:"Montserrat",Arial,sans-serif;font-size:10.5px;font-weight:600;text-transform:uppercase;display:flex;align-items:center;justify-content:center;letter-spacing:.2px}
.btn.navy{background:var(--navy)}
.photo{position:absolute}
.brand{left:160px;top:14px;display:flex;align-items:center;gap:8px}
.brand-mark{width:22px;height:22px;background:var(--navy)}
.brand-name{font-family:"Montserrat",Arial,sans-serif;font-weight:700;font-size:13px;color:var(--navy);line-height:15px;width:110px}
.contact-item{display:flex;align-items:center;gap:10px;top:28px}
.contact-icon{width:32px;height:32px;border-radius:50%;background:#f4e4e5;display:flex;align-items:center;justify-content:center}
.contact-label{font-size:11px;color:#444}
.contact-value{font-family:"Montserrat",Arial,sans-serif;font-weight:600;font-size:14px;color:var(--ink)}
.nav{left:160px;top:90px;width:880px;height:44px;background:var(--navy);display:flex;align-items:center;justify-content:space-around;padding:0 16px;z-index:2}
.nav a{color:#fff;font-family:"Montserrat",Arial,sans-serif;font-size:10.5px;text-decoration:none;position:relative}
.nav a.active{font-weight:700}
.nav a.active::after{content:"";position:absolute;left:0;right:0;bottom:-7px;height:2px;background:#fff}
.hero{left:0;top:114px;width:1200px;height:696px;background:linear-gradient(100deg,#1d3566 0%,#2a4a7c 45%,#58709a 70%,#2f4775 100%)}
.hero-title{left:160px;top:264px;font-family:"Montserrat",Arial,sans-serif;font-weight:500;font-size:44px;line-height:53px;color:#fff;width:490px}
.hero-tag{left:162px;top:425px;font-size:13px;color:#fff}
.svc-card{background:#fff;width:432px;height:346px}
.svc-title{font-family:"Montserrat",Arial,sans-serif;font-size:21px;font-weight:500;text-align:center;width:432px}
.svc-text{font-size:11.5px;line-height:14px;color:var(--muted);text-align:center;width:432px}
.band{left:0;width:1200px;background:var(--navy)}
.grid-card{width:278px;height:324px;background:#fff}
.grid-top{height:142px;padding:30px 24px}
.grid-top h3{font-family:"Montserrat",Arial,sans-serif;font-weight:500;font-size:17px;margin-bottom:10px}
.grid-top p{font-size:12px;line-height:16px;color:var(--muted);width:200px}
.grid-top .arrow{margin-top:12px;font-size:14px;color:var(--muted)}
.grid-card.accent .grid-top{background:var(--red)}
.grid-card.accent h3,.grid-card.accent p,.grid-card.accent .arrow{color:#fff}
.avatar{width:124px;height:124px;border-radius:50%}
.t-head{font-size:13.5px;line-height:18px}
.stars{color:var(--navy);font-size:11px;letter-spacing:1px;margin-left:8px}
.quote{font-family:Georgia,serif;font-size:56px;color:#d6868b;line-height:1}
.t-body{font-size:13.5px;line-height:19.5px;color:var(--muted);text-align:justify;width:270px}
.chev{font-size:22px;color:#666}
.faq{left:230px;width:740px;height:84px;border-bottom:1px solid var(--line);display:flex;align-items:center;justify-content:space-between;font-size:13px;color:#333;padding:0 4px}
.faq span:last-child{font-size:18px}
.blog{width:420px;height:324px;background:var(--card)}
.blog-body{position:absolute;left:24px;top:28px;width:250px}
.blog-tag{font-size:10.5px;color:var(--red);text-transform:uppercase}
.blog-date{font-size:10.5px;color:#777;margin-top:12px;letter-spacing:1px}
.blog-title{font-family:"Montserrat",Arial,sans-serif;font-weight:500;font-size:16px;line-height:22px;margin-top:20px}
.blog-text{font-size:11.5px;line-height:18px;color:#666;margin-top:14px;width:240px}
.blog-more{font-size:13.5px;color:var(--red);font-weight:500;margin-top:26px}
.field{width:176px;border-bottom:1px solid rgba(255,255,255,.4);height:40px;font-size:11px;color:#fff}
.foot-h{font-family:"Montserrat",Arial,sans-serif;font-size:14px;font-weight:500;color:#fff}
.foot-link{font-size:11px;color:#fff}
.social{width:14px;height:14px;border-radius:50%;background:#fff}
</style>
</head>
<body>

<div class="abs brand">
  <div class="brand-mark"></div>
  <div class="brand-name">Larkfield Ridge Management</div>
</div>
<div class="abs contact-item" style="left:516px">
  <div class="contact-icon"><svg width="14" height="14" viewBox="0 0 24 24"><path d="M6.6 10.8a15 15 0 0 0 6.6 6.6l2.2-2.2c.3-.3.7-.4 1-.2 1.1.4 2.3.6 3.6.6.6 0 1 .4 1 1V20c0 .6-.4 1-1 1C10.6 21 3 13.4 3 4c0-.6.4-1 1-1h3.5c.6 0 1 .4 1 1 0 1.2.2 2.4.6 3.6.1.3 0 .7-.2 1z" fill="#b4313a"/></svg></div>
  <div><div class="contact-label">Call Us</div><div class="contact-value">(212) 555-0184</div></div>
</div>
<div class="abs contact-item" style="left:700px">
  <div class="contact-icon"><svg width="14" height="12" viewBox="0 0 24 18"><rect x="1" y="1" width="22" height="16" rx="2" fill="none" stroke="#b4313a" stroke-width="2"/><path d="M1 2l11 8 11-8" fill="none" stroke="#b4313a" stroke-width="2"/></svg></div>
  <div><div class="contact-label">Email</div><div class="contact-value">info@larkfieldridgemanagement.com</div></div>
</div>
<nav class="abs nav">
  <a class="active" href="#">HOME</a><a href="#">ABOUT US</a><a href="#">SERVICES</a><a href="#">TESTIMONIALS</a><a href="#">PROJECTS</a><a href="#">FAQS</a><a href="#">BLOG</a><a href="#">CONTACT US</a>
</nav>

<div class="abs hero" role="img" aria-label="Modern apartment tower at dusk with a deep blue overlay"></div>
<h1 class="abs hero-title">Professional Property Management You Can Trust</h1>
<div class="abs hero-tag">A true partner, not just a vendor.</div>
<div class="btn" style="left:160px;top:464px;width:208px;height:36px">Get a Free Consultation</div>

<div class="abs svc-card" style="left:160px;top:664px"></div>
<div class="photo" style="left:172px;top:676px;width:410px;height:320px;background:linear-gradient(180deg,#6d7a82,#5a4130 60%,#2d2a26)" role="img" aria-label="Modern wood-clad residential house"></div>
<div class="abs svc-title" style="left:160px;top:1018px">Residential Property Management</div>
<div class="abs svc-text" style="left:160px;top:1058px">Gain instant access to the latest supplier catalogs and real-time<br>pricing, ensuring your team stays accurate<br>and efficient.</div>
<div class="btn" style="left:310px;top:1118px;width:132px;height:40px">View Service</div>

<div class="abs svc-card" style="left:608px;top:664px"></div>
<div class="photo" style="left:620px;top:676px;width:410px;height:320px;background:linear-gradient(180deg,#3ea3d0,#8fc7df 45%,#2b3a55 100%)" role="img" aria-label="Modern commercial apartment building under blue sky"></div>
<div class="abs svc-title" style="left:608px;top:1018px">Commercial Property Management</div>
<div class="abs svc-text" style="left:608px;top:1058px">Gain instant access to the latest supplier catalogs and real-time<br>pricing, ensuring your team stays accurate<br>and efficient.</div>
<div class="btn navy" style="left:758px;top:1118px;width:132px;height:40px">View Service</div>

<div class="abs" style="left:0;width:1200px;text-align:center;top:1230px;font-size:13px">About Us</div>
<h2 class="abs heading" style="top:1252px;font-size:29px">Our Property Management Solutions</h2>
<p class="abs" style="left:236px;width:728px;top:1308px;font-size:11.5px;line-height:18px;color:#666;text-align:center">Lorem Ipsum is simply dummy text of the printing and typesetting industry. Lorem Ipsum has been the industry's standard dummy text ever since the 1500s, when an unknown printer took a galley of type and scrambled it to make a type specimen book. It has survived not only five centuries, but also the leap into electronic typesetting, remaining essentially unchanged. It was popularised in the 1960s with the release of Corvane sheets containing Lorem Ipsum passages, and more recently with desktop publishing software like Quillset PageForm including versions of Lorem Ipsum.</p>
<div class="btn" style="left:532px;top:1422px;width:136px;height:36px">Learn More</div>

<section class="abs band" style="top:1518px;height:642px"></section>
<h2 class="abs heading" style="top:1572px;font-size:29px;color:#fff">Our Services</h2>
<p class="abs sub" style="top:1620px;color:#fff">Each year in Maricopa County, thousands of people are injured in prevent able incidents that have nothing to do with toll of personal and hospitals across the Phoenix metro area every day.</p>

<div class="abs grid-card" style="left:162px;top:1704px">
  <div class="grid-top"><h3>Residential Property</h3><p>Falls due to hazardous or are prepared to examine ...</p><div class="arrow">→</div></div>
  <div style="height:182px;background:linear-gradient(180deg,#c9d3da,#6f6a5c 60%,#3b3a33)" role="img" aria-label="White residential house among autumn trees"></div>
</div>
<div class="abs grid-card" style="left:461px;top:1704px">
  <div class="grid-top"><h3>Commercial Property</h3><p>Falls due to hazardous or are prepared to examine ...</p><div class="arrow">→</div></div>
  <div style="height:182px;background:linear-gradient(180deg,#5f9fd8,#9cc4e6 45%,#3b5672)" role="img" aria-label="Glass office towers against a blue sky"></div>
</div>
<div class="abs grid-card accent" style="left:760px;top:1704px">
  <div class="grid-top"><h3>Tenant Placement</h3><p>Falls due to hazardous or are prepared to examine ...</p><div class="arrow">→</div></div>
  <div style="height:182px;background:linear-gradient(180deg,#e6e0d6,#b9a897 55%,#6f6257)" role="img" aria-label="Agent reviewing documents with clients at a table"></div>
</div>
<div class="btn" style="left:520px;top:2066px;width:162px;height:36px">View All Services</div>

<h2 class="abs heading" style="top:2228px;font-size:29px">Our Testimonials</h2>
<p class="abs sub" style="top:2276px;color:#444">Each year in Maricopa County, thousands of people are injured in prevent able incidents that have nothing to do with toll of personal and hospitals across the Phoenix metro area every day.</p>
<div class="abs chev" style="left:102px;top:2410px">‹</div>
<div class="abs chev" style="left:1082px;top:2410px">›</div>

<div class="abs avatar" style="left:160px;top:2364px;background:radial-gradient(circle,#c9a58f,#3a2c27)" role="img" aria-label="Portrait of a smiling client"></div>
<div class="abs" style="left:304px;top:2358px">
  <div class="t-head">Dana Whitfield<span class="stars">★★★★★</span></div>
  <div class="t-head">Northgate Holdings Ltd.</div>
</div>
<div class="abs quote" style="left:476px;top:2352px">“</div>
<p class="abs t-body" style="left:304px;top:2408px">There are many variations of passages of Lorem Ipsum available, but the majority have suffered alteration in some form, by injected humour, or randomised words look even slightly believable.</p>

<div class="abs avatar" style="left:622px;top:2364px;background:radial-gradient(circle,#caa791,#e9e4e0)" role="img" aria-label="Portrait of a bearded client"></div>
<div class="abs" style="left:766px;top:2358px">
  <div class="t-head">Dana Whitfield<span class="stars">★★★★★</span></div>
  <div class="t-head">Northgate Holdings Ltd.</div>
</div>
<div class="abs quote" style="left:938px;top:2352px">“</div>
<p class="abs t-body" style="left:766px;top:2408px">There are many variations of passages of Lorem Ipsum available, but the majority have suffered alteration in some form, by injected humour, or randomised words look even slightly believable.</p>
<div class="btn" style="left:512px;top:2570px;width:176px;height:36px">View All Testimonial</div>

<section class="abs band" style="top:2680px;height:572px"></section>
<h2 class="abs heading" style="top:2738px;font-size:29px;color:#fff">Latest Projects</h2>
<p class="abs sub" style="top:2786px;color:#fff">Each year in Maricopa County, thousands of people are injured in prevent able incidents that have nothing to do with toll of personal and hospitals across the Phoenix metro area every day.</p>
<div class="photo" style="left:162px;top:2868px;width:276px;height:260px;background:linear-gradient(160deg,#5f7a4a,#8b8b7a 50%,#4b6a3c)" role="img" aria-label="Aerial view of a campus development"></div>
<div class="photo" style="left:461px;top:2868px;width:276px;height:260px;background:linear-gradient(180deg,#3a4a5c,#7a6a52 50%,#2a3440)" role="img" aria-label="Lit residential tower at night"></div>
<div class="photo" style="left:762px;top:2868px;width:276px;height:260px;background:linear-gradient(160deg,#6f8a55,#b3a58c 50%,#5a7a45)" role="img" aria-label="Aerial view of a villa complex with gardens"></div>
<div class="btn" style="left:508px;top:3166px;width:186px;height:36px">View All Projects</div>

<h2 class="abs heading" style="top:3308px;font-size:29px">FAQs</h2>
<p class="abs sub" style="top:3360px;color:#444;left:240px;width:720px">No two cases are the same, and no two cases should be handled the same way. That said, although this is not legal advice, below are a few general principles that apply to personal injury legal claims in Phoenix, Arizona.</p>
<div class="abs faq" style="top:3414px"><span>When should I speak with a personal injury attorney following an accident?</span><span>+</span></div>
<div class="abs faq" style="top:3498px"><span>How much does it cost to hire a personal injury lawyer?</span><span>+</span></div>
<div class="abs faq" style="top:3582px"><span>How much does it cost to have you investigate my personal injury legal claim?</span><span>+</span></div>
<div class="abs faq" style="top:3666px"><span>How much does it cost to have you investigate my personal injury legal claim?</span><span>+</span></div>
<div class="abs faq" style="top:3750px"><span>How much money is my personal injury claim worth?</span><span>+</span></div>
<div class="btn" style="left:536px;top:3880px;width:128px;height:36px">View All FAQ</div>

<h2 class="abs heading" style="top:3972px;font-size:29px">Latest Blog</h2>
<p class="abs sub" style="top:4022px;color:#444">Each year in Maricopa County, thousands of people are injured in prevent able incidents that have nothing to do with toll of personal and hospitals across the Phoenix metro area every day.</p>

<div class="abs blog" style="left:160px;top:4096px">
  <div class="blog-body">
    <div class="blog-tag">Larkfield Ridge Management LLC</div>
    <div class="blog-date">June 25, 2026</div>
    <div class="blog-title">5 Surprising Benefits of Naturopathic Mud Therapy...</div>
    <div class="blog-text">Consectetuer fringilla aenean sagittis potenti ullamcorper nam porta feugiat. Ante urna congue feugiat efficitur vel duis.</div>
    <div class="blog-more">Continue Reading &nbsp;→</div>
  </div>
  <div class="photo" style="left:280px;top:0;width:140px;height:324px;background:linear-gradient(180deg,#d9d5d0,#8a6d5c 50%,#3a3a3a)" role="img" aria-label="Woman with glasses reading"></div>
</div>
<div class="abs blog" style="left:620px;top:4096px">
  <div class="blog-body">
    <div class="blog-tag">Larkfield Ridge Management LLC</div>
    <div class="blog-date">June 25, 2026</div>
    <div class="blog-title">Exploring the Profound Benefits of Jal Neti...</div>
    <div class="blog-text">Consectetuer fringilla aenean sagittis potenti ullamcorper nam porta feugiat. Ante urna congue feugiat efficitur vel duis.</div>
    <div class="blog-more">Continue Reading &nbsp;→</div>
  </div>
  <div class="photo" style="left:280px;top:0;width:140px;height:324px;background:linear-gradient(180deg,#f2f0ee,#6b4a3a 55%,#d8c8b8)" role="img" aria-label="Smiling woman with curly hair"></div>
</div>
<div class="btn" style="left:536px;top:4468px;width:128px;height:36px">View All Blog</div>

<section class="abs band" style="top:4560px;height:342px"></section>
<div class="abs" style="left:160px;top:4622px;font-size:13px;color:#fff">Contact</div>
<h2 class="abs" style="left:160px;top:4644px;font-family:'Montserrat',Arial,sans-serif;font-weight:500;font-size:42px;color:#fff">Get In Touch</h2>
<div class="abs field" style="left:160px;top:4740px">First Name*</div>
<div class="abs field" style="left:376px;top:4740px">Last Name*</div>
<div class="abs field" style="left:588px;top:4740px;height:100px">Message*</div>
<div class="abs field" style="left:160px;top:4802px">Phone Number*</div>
<div class="abs field" style="left:376px;top:4802px">Email Address*</div>
<div class="btn" style="left:804px;top:4786px;width:234px;height:38px;font-size:12px">Send Message</div>

<footer class="abs" style="left:0;top:4902px;width:1200px;height:238px;background:var(--footer)"></footer>
<div class="abs" style="left:160px;top:4968px;display:flex;align-items:center;gap:8px">
  <div style="width:22px;height:22px;background:#fff"></div>
  <div style="font-family:'Montserrat',Arial,sans-serif;font-weight:700;font-size:13px;color:#fff;line-height:15px;width:110px">Larkfield Ridge Management</div>
</div>
<p class="abs" style="left:160px;top:5024px;width:260px;font-size:12px;line-height:15px;color:#fff">We help individuals and families protect their assets and loved ones with proper estate planning.</p>
<div class="abs foot-h" style="left:545px;top:4960px">Quick Links</div>
<div class="abs foot-link" style="left:545px;top:4996px">Home</div>
<div class="abs foot-link" style="left:545px;top:5024px">About Us</div>
<div class="abs foot-link" style="left:545px;top:5052px">Services</div>
<div class="abs foot-link" style="left:636px;top:4996px">Testimonial</div>
<div class="abs foot-link" style="left:636px;top:5024px">Blog</div>
<div class="abs foot-link" style="left:636px;top:5052px">Contact Us</div>
<div class="abs foot-h" style="left:846px;top:4960px">Location</div>
<svg class="abs" style="left:848px;top:4994px" width="14" height="20" viewBox="0 0 14 20"><path d="M7 0a7 7 0 0 0-7 7c0 5 7 13 7 13s7-8 7-13a7 7 0 0 0-7-7zm0 10a3 3 0 1 1 0-6 3 3 0 0 1 0 6z" fill="#fff"/></svg>
<div class="abs foot-link" style="left:878px;top:4994px;width:170px;line-height:13px">48 Harlow Ave, Fl 12 New York, NY 10016</div>
<div class="abs" style="left:160px;top:5118px;font-size:10px;color:#ddd">© 2026 by Larkfield Ridge Management LLC.</div>
<div class="abs social" style="left:948px;top:5118px"></div>
<div class="abs social" style="left:984px;top:5118px"></div>
<div class="abs social" style="left:1024px;top:5118px"></div>

</body>
</html>
```